Card Design for my dog training business Brightpaw Obedience

Need a business card design for my dog training business with my new logo. Want the card to come off professional yet fun. Want it to be very eye catchy as well. I normally have these at vet clinics, pet stores, and groomers. so need it to look better than my competitors.
Target Market(s)
dog owners
Industry/Entity Type
Dog Training
Contact Information for Business Card
needs logo, my name and info
Font styles to use
Serif
Colors
0255a3
ffffff
ec1f27
000000
333333
fbfbfb
Requirements
Must have
- Brightpaw Obedience
- Felix Orland
- 415 903 2276
- info@brightpawobedience.example
- www.brightpawobedience.example

```html
<!DOCTYPE html>
<html lang="en">
<head>
<meta charset="utf-8">
<title>Brightpaw Obedience – Business Card</title>
<link rel="stylesheet" href="https://fonts.googleapis.com/css2?family=Cinzel:wght@400&family=Cormorant+Garamond:ital,wght@0,500;1,500&family=Lato:wght@400&display=swap">
<style>
  :root {
    --backdrop: #1f1f1f;
    --card-dark: #333333;
    --card-light: #fbfbfb;
    --ink: #000000;
    --soft-text: #d6d6d6;
    --muted-text: #a9a9a9;
  }
  * { margin: 0; padding: 0; box-sizing: border-box; }
  html, body {
    width: 1200px; height: 896px; overflow: hidden;
    background: var(--backdrop);
  }
  .sheet {
    position: relative; width: 1200px; height: 896px;
    display: flex; flex-direction: column; align-items: center;
    justify-content: center; gap: 32px;
  }
  .card {
    position: relative; width: 700px; height: 400px;
    background: var(--card-dark); overflow: hidden;
    box-shadow: 0 10px 24px rgba(0,0,0,.45);
  }

  /* Front */
  .brand-panel {
    position: absolute; left: 0; top: 0; width: 270px; height: 400px;
    background: var(--card-light);
    display: flex; flex-direction: column; justify-content: center;
    padding: 0 28px 90px;
  }
  .brand-name {
    font-family: "Cormorant Garamond", serif; font-weight: 500;
    font-size: 44px; line-height: 1.05; color: var(--ink);
  }
  .brand-mark {
    width: 18px; height: 18px; background: var(--ink); margin-bottom: 16px;
  }
  .footer-band {
    position: absolute; left: 0; right: 0; bottom: 0; height: 58px;
    background: var(--card-light);
    border-top: 4px solid var(--ink);
    display: flex; align-items: center; justify-content: flex-end;
    padding-right: 30px;
  }
  .footer-band::before {
    content: ""; position: absolute; left: 270px; right: 0; top: -14px;
    height: 2px; background: var(--card-light);
  }
  .website {
    font-family: "Cormorant Garamond", serif; font-weight: 500;
    font-size: 22px; letter-spacing: 2px; color: var(--ink);
  }
  .contact {
    position: absolute; right: 30px; top: 96px; text-align: right;
    color: var(--soft-text);
  }
  .person-name {
    font-family: "Cinzel", serif; font-size: 24px; letter-spacing: 2px;
    margin-bottom: 40px; margin-right: 26px;
  }
  .contact-line {
    font-family: "Lato", sans-serif; font-size: 17px; letter-spacing: 1px;
    display: flex; align-items: center; justify-content: flex-end; gap: 10px;
    margin-bottom: 8px;
  }
  .contact-line svg { width: 16px; height: 16px; fill: var(--soft-text); flex: none; }

  /* Back */
  .card-back {
    display: flex; flex-direction: column; align-items: center; justify-content: center;
  }
  .back-name {
    font-family: "Cormorant Garamond", serif; font-weight: 500;
    font-size: 50px; color: var(--muted-text);
    padding-bottom: 10px; border-bottom: 2px solid var(--muted-text);
  }
  .tagline {
    margin-top: 22px;
    font-family: "Cormorant Garamond", serif; font-style: italic; font-weight: 500;
    font-size: 18px; color: var(--muted-text);
  }
</style>
</head>
<body>
<main class="sheet">
  <section class="card card-front" aria-label="Card front">
    <div class="brand-panel">
      <div class="brand-mark"></div>
      <p class="brand-name">Brightpaw Obedience</p>
    </div>
    <div class="contact">
      <p class="person-name">FELIX ORLAND</p>
      <p class="contact-line">415 903 2276
        <svg viewBox="0 0 24 24" aria-hidden="true"><path d="M6.6 10.8a15.1 15.1 0 0 0 6.6 6.6l2.2-2.2a1 1 0 0 1 1-.25 11.4 11.4 0 0 0 3.6.57 1 1 0 0 1 1 1V20a1 1 0 0 1-1 1A17 17 0 0 1 3 4a1 1 0 0 1 1-1h3.5a1 1 0 0 1 1 1c0 1.25.2 2.45.57 3.57a1 1 0 0 1-.25 1z"/></svg>
      </p>
      <p class="contact-line">info@brightpawobedience.example
        <svg viewBox="0 0 24 24" aria-hidden="true"><path d="M3 5h18v14H3z M4.5 6.5 12 12l7.5-5.5v-.2h-15z" fill-rule="evenodd"/></svg>
      </p>
    </div>
    <div class="footer-band">
      <p class="website">www.brightpawobedience.example</p>
    </div>
  </section>

  <section class="card card-back" aria-label="Card back">
    <p class="back-name">Brightpaw Obedience</p>
    <p class="tagline">“Good habits for happy dogs, one lesson at a time.”</p>
  </section>
</main>
</body>
</html>
```